Family business needs stationery redesign with new logo

Family owned company, established in 1987 wanting a brand 'refresh'. We are an electrical, refrigeration and construction company based in the Barkly Region Northern Territory, Australia. We have a new logo we would like to use which is uploaded along with our current letterhead and email signature. We are also dropping the word 'contractors' so please do not include this on any designs. Please note also, the 'orange' color used in our logo and designs should be Northern Territory red ochre which is as follows:

RGB (Hex): #C75B12
PantoneĀ® 159 C
CMYK: 1 / 74 / 100 / 7

We are needing our stationery redesigned using our new logo. Please include letterheads, business cards, envelopes, and email signatures.

We currently use our business letterheads for quotations, invoices, letters, HR matters, and internal memos.

We also need a separate simplified letterhead for internal paperwork such as employee leave forms, meeting agendas, and meeting minutes etc.

Reason: Needing more submissions of full package designs. We are wanting all our stationery, including business cards, letterheads, email signatures, envelopes, etc to be cohesive. We also require ALL the information, as supplied on our template letterhead, to be included on the new letterhead designs. including electrical license no.etc Thank you, R&W

Reason: needing more time as work has got in the way of looking over designs. A lot of designs not meeting the brief/criteria.

Industry/Entity Type

Business

Colors
0355a3
f37122

Requirements
Must have
• The 'orange' color used in the designs should be Northern Territory red ochre which is as follows:
• RGB (Hex): #C75B12
• PantoneĀ® 159 C
• CMYK: 1 / 74 / 100 / 7
• ***MUST INCLUDE ALL INFORMATION THAT IS ON OUR CURRENT LETTERHEAD***
Should not have
• Please do not include the word 'contractors'

```html
<!DOCTYPE html>
<html lang="en">
<head>
<meta charset="utf-8">
<title>R&amp;W Business Card</title>
<link href="https://fonts.googleapis.com/css2?family=Arimo:wght@400;700&display=swap" rel="stylesheet">
<style>
  :root {
    --page-bg: #e6e7ea;
    --card-bg: #f3f4f5;
    --card-edge: #d5d8dc;
    --navy-deep: #0d143e;
    --navy: #1c2a6b;
    --ochre: #c75b12;
    --panel-text: #e8ebf4;
  }
  * { margin: 0; padding: 0; box-sizing: border-box; }
  html, body {
    width: 1200px;
    height: 969px;
    overflow: hidden;
    background: var(--page-bg);
    font-family: "Arimo", Arial, sans-serif;
  }
  .business-card {
    position: absolute;
    left: 120px;
    top: 211px;
    width: 960px;
    height: 546px;
    border-radius: 26px;
    background: var(--card-bg);
    border: 1px solid var(--card-edge);
    overflow: hidden;
    box-shadow: 0 18px 40px rgba(20, 25, 50, 0.16);
  }
  .card-panel {
    position: absolute;
    inset: 0;
  }
  .brand-name {
    position: absolute;
    left: 212px;
    top: 290px;
    transform: translate(-50%, -50%);
    font-weight: 700;
    font-size: 84px;
    letter-spacing: 2px;
    color: var(--navy);
  }
  .contact-block {
    position: absolute;
    right: 74px;
    top: 112px;
    text-align: right;
    color: var(--panel-text);
  }
  .person-name {
    font-weight: 700;
    font-size: 31px;
    letter-spacing: 1px;
    color: var(--ochre);
  }
  .person-title {
    font-size: 23px;
    margin-top: 8px;
  }
  .address {
    font-size: 24px;
    line-height: 34px;
    margin-top: 42px;
  }
  .contact-list {
    list-style: none;
    margin-top: 36px;
  }
  .contact-list li {
    display: flex;
    justify-content: flex-end;
    align-items: center;
    font-size: 22px;
    height: 37.5px;
  }
  .contact-list svg {
    width: 22px;
    height: 22px;
    margin-left: 14px;
    margin-right: -38px;
    fill: var(--ochre);
  }
  .contact-list li span { margin-right: 2px; }
</style>
</head>
<body>
  <div class="business-card">
    <svg class="card-panel" viewBox="0 0 960 546" width="960" height="546">
      <defs>
        <linearGradient id="panelShade" x1="0" y1="0" x2="1" y2="1">
          <stop offset="0" stop-color="#1d2a6c"/>
          <stop offset="1" stop-color="#0b1138"/>
        </linearGradient>
      </defs>
      <path d="M790 0 C380 40 380 470 700 546 L960 546 L960 0 Z" fill="url(#panelShade)"/>
      <path d="M778 6 C398 50 398 466 712 546" fill="none" stroke="var(--ochre)" stroke-width="5"/>
    </svg>

    <div class="brand-name">R&amp;W</div>

    <div class="contact-block">
      <div class="person-name">DANIEL HARLOW</div>
      <div class="person-title">CEO/Founder</div>
      <div class="address">214 Ironbark Street<br>Tennant Creek, NT 0860</div>
      <ul class="contact-list">
        <li><span>708 512 3946</span>
          <svg viewBox="0 0 24 24" aria-label="Phone"><path d="M6.6 10.8a15.1 15.1 0 0 0 6.6 6.6l2.2-2.2c.3-.3.7-.4 1-.2 1.1.4 2.3.6 3.6.6.6 0 1 .4 1 1V20c0 .6-.4 1-1 1C10.6 21 3 13.4 3 4c0-.6.4-1 1-1h3.5c.6 0 1 .4 1 1 0 1.3.2 2.5.6 3.6.1.3 0 .7-.2 1z"/></svg></li>
        <li><span>708 512 3947</span>
          <svg viewBox="0 0 24 24" aria-label="Fax"><path d="M6 3h10v5H6zM3 9h18v8h-3v4H6v-4H3zm5 6v4h8v-4zm10-4a1 1 0 1 0 0 2 1 1 0 0 0 0-2z"/></svg></li>
        <li><span>office@rwelectric.com</span>
          <svg viewBox="0 0 24 24" aria-label="Email"><path d="M2 5h20v14H2zm2 2v.5l8 5.5 8-5.5V7zm0 3v7h16v-7l-8 5.5z"/></svg></li>
        <li><span>www.rwelectric.com</span>
          <svg viewBox="0 0 24 24" aria-label="Website"><path d="M12 2a10 10 0 1 0 0 20 10 10 0 0 0 0-20zm-1 17.9A8 8 0 0 1 4.2 10.5L9 15v1a2 2 0 0 0 2 2zm6.9-2.5A2 2 0 0 0 16 16h-1v-3a1 1 0 0 0-1-1H8v-2h2a1 1 0 0 0 1-1V7h2a2 2 0 0 0 2-2v-.4a8 8 0 0 1 2.9 12.8z"/></svg></li>
      </ul>
    </div>
  </div>
</body>
</html>
```